Veldmark Supplies Business Card

Professional business card that stand out to our potential customers. Front and back with clean modern design

Industry/Entity Type

Oil and gas

Contact Information for Business Card

Name, address, website , office phone and cell number

Requirements
Must have
• Editable files for each employee

```html
<!DOCTYPE html>
<html lang="en">
<head>
<meta charset="utf-8">
<title>Veldmark Supplies Business Card</title>
<link rel="stylesheet" href="https://fonts.googleapis.com/css2?family=Michroma&family=Poppins:wght@400;500&display=swap">
<style>
  :root {
    --stage: #2a2b2d;
    --card: #1c1d1f;
    --card-deep: #111213;
    --red: #f20d0d;
    --blue: #14a9cc;
    --ink: #ffffff;
    --rule: #8a8b8d;
  }
  * { box-sizing: border-box; margin: 0; padding: 0; }
  html, body { width: 1200px; height: 1108px; overflow: hidden; }
  body {
    background: var(--stage);
    font-family: "Poppins", sans-serif;
    color: var(--ink);
    position: relative;
  }
  .card {
    position: absolute;
    top: 214px;
    width: 440px;
    height: 680px;
    border-radius: 22px;
    background: var(--card);
    overflow: hidden;
  }
  .card--front { left: 120px; }
  .card--back { left: 640px; }

  .brand {
    position: absolute;
    top: 150px;
    left: 0; right: 0;
    display: flex;
    align-items: center;
    justify-content: center;
    gap: 14px;
  }
  .brand__mark { width: 30px; height: 30px; background: var(--red); }
  .brand__name {
    font-family: "Michroma", sans-serif;
    font-size: 26px;
    color: var(--ink);
    letter-spacing: 0.5px;
  }

  .person {
    position: absolute;
    top: 330px;
    left: 0; right: 0;
    text-align: center;
    font-family: "Michroma", sans-serif;
    font-size: 28px;
    letter-spacing: 1px;
    text-transform: uppercase;
  }
  .person__first { color: var(--red); }
  .person__last { color: var(--blue); }

  .icons {
    position: absolute;
    top: 405px;
    left: 40px; right: 40px;
    display: flex;
    align-items: center;
    gap: 8px;
  }
  .icons__rule { flex: 1; height: 1px; background: var(--rule); }
  .icon {
    width: 34px; height: 34px;
    border-radius: 5px;
    background: var(--red);
    display: flex; align-items: center; justify-content: center;
  }
  .icon svg { width: 20px; height: 20px; }

  .contact {
    position: absolute;
    top: 455px;
    left: 0; right: 0;
    text-align: center;
    font-size: 21px;
    line-height: 29px;
  }
  .divider {
    position: absolute;
    top: 560px;
    left: 80px; right: 80px;
    height: 1px;
    background: var(--rule);
  }
  .address {
    position: absolute;
    top: 578px;
    left: 0; right: 0;
    text-align: center;
    font-size: 19px;
    line-height: 27px;
  }

  .backdrop {
    position: absolute;
    inset: 0;
    background: linear-gradient(200deg, #6a6b6d 0%, #3a3b3d 40%, var(--card-deep) 100%);
  }
  .back-brand {
    position: absolute;
    left: 0; right: 0;
    bottom: 130px;
    display: flex;
    align-items: center;
    justify-content: center;
    gap: 8px;
  }
  .back-brand__mark { width: 14px; height: 14px; background: var(--red); }
  .back-brand__name {
    font-family: "Michroma", sans-serif;
    font-size: 13px;
    color: var(--ink);
  }
</style>
</head>
<body>
  <section class="card card--front">
    <div class="brand">
      <span class="brand__mark"></span>
      <span class="brand__name">Veldmark Supplies</span>
    </div>

    <h1 class="person"><span class="person__first">Marcus</span> <span class="person__last">Hale</span></h1>

    <div class="icons">
      <span class="icons__rule"></span>
      <span class="icon" aria-label="Office phone">
        <svg viewBox="0 0 24 24" fill="#fff"><path d="M4 9c0-3 3-5 8-5s8 2 8 5l-3 1-1-2c-2-1-6-1-8 0l-1 2zM7 12h10l2 8H5z"/></svg>
      </span>
      <span class="icon" aria-label="Mobile phone">
        <svg viewBox="0 0 24 24" fill="none" stroke="#fff" stroke-width="2"><rect x="7" y="3" width="10" height="18" rx="2"/><line x1="11" y1="18" x2="13" y2="18"/></svg>
      </span>
      <span class="icon" aria-label="Website">
        <svg viewBox="0 0 24 24" fill="none" stroke="#fff" stroke-width="2"><circle cx="12" cy="12" r="8"/><path d="M4 12h16M12 4c3 3 3 13 0 16M12 4c-3 3-3 13 0 16"/></svg>
      </span>
      <span class="icons__rule"></span>
    </div>

    <p class="contact">044-123 456 789<br>044-123 456 789<br>www.websitename.com</p>
    <div class="divider"></div>
    <p class="address">421, Address line goes here<br>45452,Country Name</p>
  </section>

  <section class="card card--back">
    <div class="backdrop" role="img" aria-label="Repeating embossed brand pattern in glossy black and grey"></div>
    <div class="back-brand">
      <span class="back-brand__mark"></span>
      <span class="back-brand__name">Veldmark Supplies</span>
    </div>
  </section>
</body>
</html>
```